Website for software company "velora"

We need a website for our software company/startup named "velora". We are developing several products (currently 3 standard-software products) which are all in different sectors, but all our products are available for Laptops/PC/Mobile Phones/Tablets, ... We do also create custom software and support our customers with consulting to optimize their processes.
We already have a Logo which you can find in the attached files.
We are a young team of 4 members (two founders and 2 employees).

To get an idea of our products -> the first one is a planning software for healthcare organizations (eg. BlueHaven, firebrigade, pharmacy), the second one is a booking software for sport clubs and the third one is a competition software for sports hunting. You see very diverse. Include or ignore this info of our products as you like.

The design has to be a bootstrap 4 (or higher) design. We have licenced FontAwesome as iconset. Responsive design should come without saying.

• Starting page, product pages, news section, contact, team, services

```html
<!DOCTYPE html>
<html lang="en">
<head>
<meta charset="utf-8">
<title>Velora — Software &amp; Process Consulting</title>
<link href="https://fonts.googleapis.com/css2?family=Montserrat:wght@300;400;500;600;700;800&display=swap" rel="stylesheet">
<style>
:root{
  --orange:#f7812a;
  --orange-deep:#f06a1c;
  --navy:#1f2632;
  --navy-2:#262e3b;
  --ink:#1d1f24;
  --text:#4a4d55;
  --muted:#8a8f99;
  --light:#f6f7f9;
  --line:#e3e5ea;
  --white:#ffffff;
}
*{box-sizing:border-box;margin:0;padding:0}
html,body{width:1200px;height:4926px;overflow:hidden}
body{font-family:"Montserrat",sans-serif;color:var(--text);background:var(--white);position:relative}
.abs{position:absolute}
.btn{position:absolute;display:flex;align-items:center;justify-content:center;border-radius:22px;background:var(--orange);color:#fff;font-weight:700;font-size:13px;letter-spacing:.5px;text-transform:uppercase}
.btn-dark{background:var(--navy)}
.brand{display:flex;align-items:center;gap:10px;font-weight:800;color:var(--ink);letter-spacing:1px}
.brand-dot{width:16px;height:16px;background:var(--orange)}
.placeholder{position:absolute}

/* header */
.site-header{position:absolute;left:0;top:0;width:1200px;height:78px;background:#fff;border-bottom:1px solid var(--line)}
.site-header .brand{position:absolute;left:134px;top:20px;font-size:38px}
.nav a{position:absolute;top:31px;font-size:12px;font-weight:600;color:var(--ink);text-decoration:none}
.nav a.active::after{content:"";position:absolute;left:0;right:0;bottom:-10px;height:2px;background:var(--orange)}
.nav .btn{left:961px;top:23px;width:122px;height:34px;font-size:12px}

/* hero */
.hero{position:absolute;left:0;top:78px;width:1200px;height:585px;background:linear-gradient(90deg,#1c232d 0%,#2a323d 45%,#4a4f55 100%)}
.hero-photo{left:480px;top:0;width:720px;height:585px;background:linear-gradient(120deg,#3b4048 0%,#7a7d80 45%,#a07a55 100%)}
.hero-kicker{left:117px;top:162px;font-size:26px;font-weight:400;color:#fff;letter-spacing:.5px}
.hero-title{left:117px;top:194px;font-size:38px;font-weight:800;color:#fff;line-height:40px}
.hero-text{left:120px;top:282px;width:370px;font-size:13px;line-height:21px;color:#c8ccd3}
.hero .btn{left:117px;top:346px;width:166px;height:42px}

/* about */
.about{position:absolute;left:0;top:663px;width:1200px;height:693px;background:linear-gradient(180deg,#f7f8fa 0%,#fbfbfc 70%,#f3efe9 100%)}
.eyebrow{position:absolute;left:0;width:1200px;text-align:center;font-size:13px;color:var(--orange);letter-spacing:.5px}
.section-title{position:absolute;left:0;width:1200px;text-align:center;font-size:34px;font-weight:300;color:var(--ink);letter-spacing:.5px}
.section-title b{font-weight:800}
.title-rule{position:absolute;left:572px;width:56px;height:3px;background:var(--orange)}
.about-text{left:254px;top:124px;width:702px;text-align:center;font-size:14px;line-height:24px;color:var(--text)}
.about-laptop{left:153px;top:216px;width:382px;height:344px;background:linear-gradient(160deg,#e9ecf1,#c9ced8);border-radius:10px}
.feature{position:absolute;padding:32px 32px;border-radius:6px;box-shadow:0 10px 30px rgba(0,0,0,.08)}
.feature h3{font-size:15px;font-weight:700;margin:18px 0 10px}
.feature p{font-size:11.5px;line-height:17px}
.feature svg{display:block}
.f-optimize{left:581px;top:218px;width:229px;height:176px;background:#fff;color:var(--ink)}
.f-optimize p{color:var(--text)}
.f-support{left:585px;top:415px;width:229px;height:176px;background:var(--orange);color:#fff}
.f-develop{left:835px;top:321px;width:229px;height:176px;background:var(--navy);color:#fff}

/* products */
.products{position:absolute;left:0;top:1356px;width:1200px;height:1554px;background:#fff}
.timeline{left:607px;top:285px;width:2px;height:987px;background:#d9dce2}
.tl-dot{position:absolute;width:58px;height:58px;border-radius:50%;display:flex;align-items:center;justify-content:center}
.tl-dot.orange{background:var(--orange);box-shadow:0 0 0 6px #fde3cf}
.tl-dot.dark{background:var(--navy);box-shadow:0 0 0 6px #e2e4e8}
.product h2{position:absolute;font-size:28px;font-weight:700;color:var(--ink);letter-spacing:.3px}
.product p{position:absolute;width:410px;font-size:14px;line-height:25px;color:var(--text)}
.product .btn{width:158px;height:44px}
.device{background:linear-gradient(160deg,#f2f3f6,#d7dbe2);border-radius:8px}

/* services */
.services{position:absolute;left:0;top:2910px;width:1200px;height:620px;background:radial-gradient(ellipse at 50% 60%,#2a3241 0%,var(--navy) 70%)}
.services .section-title,.news .section-title{color:#fff}
.service{position:absolute;width:230px}
.service h4{font-size:14px;font-weight:700;color:#fff;letter-spacing:1px;margin-bottom:6px}
.service p{font-size:10.5px;line-height:17px;color:#8d95a3}
.service.right-align{text-align:right}

/* news */
.news{position:absolute;left:0;top:3530px;width:1200px;height:587px;background:#fff}
.news-title{left:151px;top:50px;font-size:34px;font-weight:300;color:var(--ink)}
.news-title b{font-weight:800}
.news-main{left:151px;top:130px;width:470px;height:372px;background:linear-gradient(160deg,#3a4a3e,#1f2a2d 60%,#151a1f)}
.date{display:inline-block;background:var(--orange);color:#fff;font-size:10px;font-weight:700;padding:5px 12px;border-radius:2px}
.news-main .cap{position:absolute;left:36px;bottom:36px;width:410px;color:#fff}
.news-main .cap h3{font-size:15px;font-weight:700;line-height:21px;margin-top:12px}
.news-card{position:absolute;left:629px;width:435px;height:177px;border:1px solid var(--line);background:#fff}
.news-card .thumb{position:absolute;left:0;top:0;width:208px;height:175px}
.news-card .body{position:absolute;left:230px;top:30px;width:185px}
.news-card h4{font-size:12px;font-weight:700;color:var(--ink);margin:12px 0 8px}
.news-card p{font-size:11px;line-height:19px;color:var(--text)}

/* contact */
.contact{position:absolute;left:0;top:4117px;width:1200px;height:458px;background:linear-gradient(135deg,#f47a2a 0%,#f2631a 50%,#f57a2e 100%)}
.contact .section-title{color:#fff}
.contact .title-rule{background:#fff}
.field{position:absolute;background:#fff;font-size:11.5px;color:var(--ink);padding:16px 16px}
.contact .btn{left:524px;top:349px;width:151px;height:40px;font-size:12px}

/* footer */
.site-footer{position:absolute;left:0;top:4575px;width:1200px;height:351px;background:#fff}
.site-footer .brand{position:absolute;left:147px;top:86px;font-size:36px}
.foot-about{left:147px;top:137px;width:230px;font-size:10.5px;line-height:15px;color:var(--muted)}
.vrule{position:absolute;top:59px;width:1px;height:163px;background:var(--line)}
.foot-col h5{position:absolute;font-size:12px;font-weight:700;color:var(--ink);letter-spacing:.5px}
.foot-col a{position:absolute;font-size:12px;color:var(--text);text-decoration:none}
.social{position:absolute;top:94px;width:30px;height:30px;border-radius:50%;background:var(--ink)}
.copyright{left:0;top:279px;width:1200px;border-top:1px solid var(--line);padding-top:18px;text-align:center;font-size:10.5px;color:var(--text)}
</style>
</head>
<body>

<header class="site-header">
  <div class="brand"><span class="brand-dot"></span>VELORA</div>
  <nav class="nav">
    <a href="#products" class="active" style="left:421px">PRODUCT</a>
    <a href="#services" style="left:544px">SERVICES</a>
    <a href="#news" style="left:668px">NEWS</a>
    <a href="#team" style="left:767px">TEAM</a>
    <a href="#about" style="left:863px">ABOUT</a>
    <a href="#contact" class="btn">CONTACT</a>
  </nav>
</header>

<section class="hero">
  <div class="placeholder hero-photo" role="img" aria-label="Photo of a young professional in glasses working on a tablet at a desk with a coffee cup, with floating chart widgets"></div>
  <div class="abs hero-kicker">WE HELP CUSTOMER</div>
  <h1 class="abs hero-title">TO OPTIMIZE THEIR<br>PROCESSES</h1>
  <p class="abs hero-text">Lorem ipsum dolor sit amet, consectetur adipiscing elit, sed do eiusmod tempor incididunt.</p>
  <a class="btn" href="#about">LEARN MORE</a>
</section>

<section class="about" id="about">
  <div class="eyebrow" style="top:52px">WHY WE ARE</div>
  <h2 class="section-title" style="top:73px">ABOUT <b>VELORA</b></h2>
  <p class="abs about-text">Lorem ipsum dolor sit amet, consectetur adipiscing elit, sed do eiusmod tempor incididunt ut laborLorem ipsum dolor sit amet, consectetur adipiscing elit, sed do eiusmo</p>
  <div class="placeholder about-laptop" role="img" aria-label="Illustration of an open laptop showing a dashboard"></div>

  <div class="feature f-optimize">
    <svg width="34" height="34" viewBox="0 0 34 34" fill="none" stroke="#f7812a" stroke-width="2"><circle cx="17" cy="17" r="14"/><circle cx="17" cy="17" r="8"/><circle cx="17" cy="17" r="2.5"/></svg>
    <h3>OPTIMIZE</h3>
    <p>Lorem ipsum dolor sit amet, consectetur adipiscing elit, sed do eiusmod tempo</p>
  </div>
  <div class="feature f-support">
    <svg width="34" height="34" viewBox="0 0 34 34" fill="none" stroke="#fff" stroke-width="2"><circle cx="17" cy="12" r="6"/><path d="M4 28c4-4 8-5 13-3s9 1 13-3"/></svg>
    <h3>SUPPORT</h3>
    <p>Lorem ipsum dolor sit amet, consectetur adipiscing elit, sed do eiusmod tempo</p>
  </div>
  <div class="feature f-develop">
    <svg width="34" height="34" viewBox="0 0 34 34" fill="none" stroke="#f7812a" stroke-width="2"><rect x="3" y="6" width="28" height="18" rx="2"/><path d="M13 12l-3 3 3 3M21 12l3 3-3 3M12 29h10"/></svg>
    <h3>DEVELOP</h3>
    <p>Lorem ipsum dolor sit amet, consectetur adipiscing elit, sed do eiusmod tempo</p>
  </div>
</section>

<section class="products" id="products">
  <h2 class="section-title" style="top:80px">OUR <b>PRODUCTS</b></h2>
  <div class="title-rule" style="top:130px"></div>
  <div class="abs timeline"></div>

  <div class="tl-dot orange" style="left:579px;top:256px"><svg width="24" height="24" viewBox="0 0 24 24" fill="none" stroke="#fff" stroke-width="1.8"><rect x="5" y="3" width="14" height="18" rx="1"/><path d="M8 8h8M8 12h8M8 16h5"/></svg></div>
  <div class="tl-dot dark" style="left:579px;top:709px"><svg width="24" height="24" viewBox="0 0 24 24" fill="none" stroke="#fff" stroke-width="1.8"><circle cx="12" cy="12" r="9"/><circle cx="12" cy="12" r="4"/></svg></div>
  <div class="tl-dot orange" style="left:579px;top:1243px"><svg width="24" height="24" viewBox="0 0 24 24" fill="none" stroke="#fff" stroke-width="1.8"><rect x="3" y="5" width="18" height="16" rx="1"/><path d="M3 10h18M8 3v4M16 3v4"/></svg></div>

  <article class="product">
    <h2 style="left:136px;top:244px">PLANNING SOFTWARE</h2>
    <p style="left:136px;top:290px">Lorem ipsum dolor sit amet, consectetur adipiscing elit, sed do eiusmod tempor incididunt ut labore et dolore magna aliqua. Ut enim ad minim veniam, quis nostrud exercitation ullamco laboris nisi ut aliquip ex ea</p>
    <a class="btn" href="#" style="left:136px;top:421px">LEARN MORE</a>
    <div class="placeholder device" style="left:650px;top:144px;width:477px;height:373px" role="img" aria-label="Desktop monitor and keyboard showing the planning software dashboard"></div>
  </article>

  <article class="product">
    <div class="placeholder device" style="left:57px;top:632px;width:516px;height:343px" role="img" aria-label="Tablet with keyboard showing the booking software dashboard"></div>
    <h2 style="left:692px;top:713px">BOOKING SOFTWARE</h2>
    <p style="left:692px;top:757px">Lorem ipsum dolor sit amet, consectetur adipiscing elit, sed do eiusmod tempor incididunt ut labore et dolore magna aliqua. Ut enim ad minim veniam, quis nostrud exercitation ullamco laboris nisi ut aliquip ex ea</p>
    <a class="btn" href="#" style="left:688px;top:893px">LEARN MORE</a>
  </article>

  <article class="product">
    <h2 style="left:136px;top:1194px">COMPETITION SOFTWARE</h2>
    <p style="left:136px;top:1238px">Lorem ipsum dolor sit amet, consectetur adipiscing elit, sed do eiusmod tempor incididunt ut labore et dolore magna aliqua. Ut enim ad minim veniam, quis nostrud exercitation ullamco laboris nisi ut aliquip</p>
    <a class="btn" href="#" style="left:134px;top:1377px">LEARN MORE</a>
    <div class="placeholder device" style="left:669px;top:1138px;width:430px;height:306px" role="img" aria-label="Tablet and phone showing competition results tables"></div>
  </article>
</section>

<section class="services" id="services">
  <h2 class="section-title" style="top:66px">OUR <b>SERVICES</b></h2>
  <div class="title-rule" style="top:108px"></div>

  <svg class="abs" style="left:0;top:0" width="1200" height="620" viewBox="0 0 1200 620" fill="none">
    <g stroke="#c9ced6" stroke-width="1.3">
      <path d="M415 234H468L493 247"/>
      <path d="M793 234H730L705 247"/>
      <path d="M417 429H468L493 403"/>
      <path d="M789 429H730L705 403"/>
    </g>
    <g fill="#fff"><circle cx="493" cy="247" r="4"/><circle cx="705" cy="247" r="4"/><circle cx="493" cy="403" r="4"/><circle cx="705" cy="403" r="4"/></g>
    <circle cx="598" cy="325" r="130" fill="#2d3543" stroke="#454d5b" stroke-width="2"/>
    <circle cx="598" cy="325" r="109" fill="#f7812a"/>
    <g stroke="#b9bfc9" stroke-width="1.5" fill="none">
      <circle cx="386" cy="234" r="29"/><circle cx="822" cy="234" r="29"/>
      <circle cx="388" cy="429" r="29"/><circle cx="818" cy="429" r="29"/>
    </g>
    <g stroke="#e3e6eb" stroke-width="1.6" fill="none">
      <rect x="374" y="223" width="24" height="18"/><path d="M380 246h12M386 241v5"/>
      <rect x="809" y="224" width="26" height="20"/><path d="M809 230h26"/>
      <rect x="379" y="415" width="18" height="28" rx="2"/><path d="M385 438h6"/>
      <path d="M805 442h26M809 438v-10M816 438v-16M823 438v-7"/>
    </g>
  </svg>

  <div class="service right-align" style="left:106px;top:197px"><h4>SOFTWARE</h4><p>Lorem Ipsum is simply dummy text of the printing typesettinLorem Lorem Ipsum is simply dummy</p></div>
  <div class="service" style="left:866px;top:198px"><h4>BOOKING SOFTWARE</h4><p>Lorem Ipsum is simply dummy text of the printing typesettinLorem Lorem Ipsum is simply dummy</p></div>
  <div class="service right-align" style="left:111px;top:394px"><h4>MOBILE APP</h4><p>Lorem Ipsum is simply dummy text of the printing typesettinLorem Lorem Ipsum is simply dummy</p></div>
  <div class="service" style="left:870px;top:397px"><h4>ANALYTICS</h4><p>Lorem Ipsum is simply dummy text of the printing typesettinLorem Lorem Ipsum is simply dummy</p></div>

  <a class="btn" href="#" style="left:520px;top:501px;width:156px;height:40px">LEARN MORE</a>
</section>

<section class="news" id="news">
  <h2 class="abs news-title">LATEST <b>NEWS</b></h2>
  <div class="placeholder news-main" role="img" aria-label="Photo of an office workspace with plants and monitors showing code">
    <div class="cap"><span class="date">28 MAY 2021</span><h3>Lorem ipsum dolor sit amet, consectetur adipiscing elit, sed do eiusmod tempor</h3></div>
  </div>
  <div class="news-card" style="top:130px">
    <div class="thumb" role="img" aria-label="Photo of hands typing at a desk with code on monitors" style="background:linear-gradient(150deg,#4a5058,#23282e 55%,#b07a4a)"></div>
    <div class="body"><span class="date">19 MAY 2021</span><h4>Lorem ipsum dolor sit</h4><p>Duis aute irure dolor in reprehenderit in voluptate velit esse cillum dolore eu fugiat</p></div>
  </div>
  <div class="news-card" style="top:321px">
    <div class="thumb" role="img" aria-label="Photo of a developer working at multiple screens in a blue-lit room" style="background:linear-gradient(150deg,#27406a,#182236 60%,#3a5a8a)"></div>
    <div class="body"><span class="date">18 MAY 2021</span><h4>Lorem ipsum dolor sit</h4><p>Duis aute irure dolor in reprehenderit in voluptate velit esse cillum dolore eu fugiat</p></div>
  </div>
</section>

<section class="contact" id="contact">
  <h2 class="section-title" style="top:70px">CONTACT <b>VELORA</b></h2>
  <div class="title-rule" style="top:118px"></div>
  <div class="field" style="left:220px;top:148px;width:372px;height:48px">Name*</div>
  <div class="field" style="left:220px;top:210px;width:372px;height:48px">Email address*</div>
  <div class="field" style="left:220px;top:271px;width:372px;height:49px">Phone*</div>
  <div class="field" style="left:602px;top:148px;width:374px;height:172px">Message</div>
  <a class="btn btn-dark" href="#">CONTACT US</a>
</section>

<footer class="site-footer">
  <div class="brand"><span class="brand-dot"></span>VELORA</div>
  <p class="abs foot-about">Lorem ipsum dolor sit amet, consectetur adipiscing elit, sed do eiusmod tempor incididunt ut labore et dolore</p>
  <div class="vrule" style="left:428px"></div>
  <div class="vrule" style="left:657px"></div>
  <div class="vrule" style="left:883px"></div>
  <div class="foot-col">
    <h5 style="left:470px;top:62px">NAVIGATION</h5>
    <a href="#about" style="left:470px;top:96px">About Us</a>
    <a href="#products" style="left:470px;top:125px">Products</a>
    <a href="#services" style="left:470px;top:154px">Services</a>
    <a href="#contact" style="left:470px;top:182px">Contact Us</a>
  </div>
  <div class="foot-col">
    <h5 style="left:705px;top:62px">RESOURCES</h5>
    <a href="#news" style="left:706px;top:96px">News</a>
    <a href="#team" style="left:706px;top:125px">Team</a>
    <a href="#" style="left:706px;top:154px">Privacy Policy</a>
    <h5 style="left:915px;top:62px">FOLLOW US</h5>
  </div>
  <span class="social" style="left:914px;background:var(--orange)"></span>
  <span class="social" style="left:948px"></span>
  <span class="social" style="left:983px"></span>
  <span class="social" style="left:1017px"></span>
  <div class="abs copyright">© 2022 Velora | All Rights Reserved</div>
</footer>

</body>
</html>
```